January 2013 Flyer

Hi,

Flyer for a winter flooring sale.
Warm and cozy look.
It should be professional, clean, not cluttered. Nice color.

Our clients have expensive homes in a modern west coast contemporary design. Clean lines and colours.

The flyer should represent that style.

Target Market(s)

Mid to High income house owners
30-65yrs old.
Often baby boomers whose kids have left and finally can renovate the way they've always wanted.

Industry/Entity Type

Flooring

Requirements
Must have
• 1) The Larchvale Surfaces logo and contact info.
2) It must have the at least one of the Quillmark logo provided, displayed in the carpet sale section.
3) KTRSG, PQHU, and OZJ logos

www.larchvalesurfaces.example

As well as OZJ, PQHU, as well as Rimhold Surface covering guild logo.

Specials on Quillmark Carpet:
Multicolor Berber Carpet - 2 Styles, 24 colors
$2.39 $ 1.59

35oz Plush Velmora Carpet - 2 Styles, 30 Colors $2.89 $ 1.99

Patterned Velmora Carpet, 12 Colors
$2.99 $ 1.99

50oz Freize Velmora Carpet, 2 Styles - 28 Colors $2.99 $ 2.39

Dustquell Berber Carpet - 12 Colors
$3.59 $ 2.39

5” Designer engineered hardwood - 10 different styles
$6.25 $4.99

12” X 36” Swiss-made Commercial-grade vinyl cork planking
$6.75 $3.99

I have more files but its too big to put on here such as: room scenes
Nice to have
• Our clients have homes in a modern west coast contemporary design. Clean lines and colours.

Should not have
• I don't want an old simple flyer. Colours shouldn't be boring,

```html
<!DOCTYPE html>
<html lang="en">
<head>
<meta charset="utf-8">
<title>Larchvale Surfaces – Winter Flooring Sale Flyer</title>
<link rel="stylesheet" href="https://fonts.googleapis.com/css2?family=Open+Sans:wght@300;400;600;700;800&display=swap">
<style>
  :root {
    --stage: #1f1f20;
    --sale-red: #e31e26;
    --price-red: #e8332a;
    --ink: #333333;
    --muted: #6b6b6b;
    --navy: #1d2a7a;
    --paper: #ffffff;
    --footer-grey: #5d5d61;
    --carpet-light: #f3efe6;
    --carpet-shade: #d9d1c1;
    --wood-light: #9a6a44;
    --wood-dark: #5e3b22;
    --room-light: #ebe7e1;
    --room-wood: #7a3a20;
  }
  * { box-sizing: border-box; margin: 0; padding: 0; }
  html, body { width: 1200px; height: 793px; overflow: hidden; }
  body {
    background: var(--stage);
    font-family: "Open Sans", Arial, sans-serif;
    position: relative;
  }

  /* ---------- price list flyer ---------- */
  .price-flyer {
    position: absolute; left: 225px; top: 72px;
    width: 330px; height: 648px;
    background: var(--paper);
    overflow: hidden;
  }
  .price-flyer__carpet {
    position: absolute; left: 0; top: 60px; width: 100%; height: 318px;
    background: radial-gradient(circle at 40% 40%, var(--carpet-light), var(--carpet-shade));
  }
  .price-flyer__wood {
    position: absolute; left: 0; top: 378px; width: 100%; height: 200px;
    background: linear-gradient(100deg, var(--wood-light), var(--wood-dark) 55%, var(--wood-light));
  }
  .brand-header {
    position: absolute; left: 0; top: 0; width: 100%; height: 60px;
    background: var(--paper);
  }
  .brand-header__name {
    position: absolute; right: 22px; top: 14px;
    font-size: 19px; font-weight: 400; letter-spacing: 2.2px;
    color: var(--navy);
  }
  .brand-header__rule {
    position: absolute; left: 58px; right: 14px; top: 43px;
    border-top: 1px solid var(--navy);
  }
  .brand-header__mark {
    position: absolute; left: 14px; top: 14px; width: 22px; height: 22px;
    background: var(--sale-red);
  }

  .special {
    position: absolute; left: 20px; right: 16px;
    border-bottom: 1px dashed rgba(255,255,255,.9);
    color: var(--ink);
  }
  .special__name { font-size: 11px; text-transform: uppercase; line-height: 1.2; }
  .special__detail { font-size: 9px; }
  .special__was {
    position: absolute; font-size: 10px; color: var(--muted);
    text-decoration: line-through;
  }
  .special__now {
    position: absolute; right: 0; color: var(--price-red);
    font-weight: 400; line-height: 1;
    text-shadow: 0 0 3px #fff, 0 0 2px #fff;
    white-space: nowrap;
  }
  .special__now .cents {
    display: inline-block; vertical-align: top; text-align: left;
    line-height: .9;
  }
  .special__now .unit { display: block; font-weight: 700; }
  .special--wood { color: #fff; border-bottom-color: rgba(255,255,255,.8); }
  .special--wood .special__was { color: #e6d6c6; }
  .origin-tag {
    display: inline-block; width: 38px; height: 12px; margin-top: 3px;
    background: var(--sale-red);
  }

  .member-strip {
    position: absolute; left: 16px; right: 16px; top: 500px; height: 72px;
    background: var(--paper); border-radius: 8px;
    display: flex; align-items: center; justify-content: space-around;
    padding: 0 6px;
  }
  .member-strip__badge { display: block; background: #2f4f9a; }
  .member-strip__badge--tall { width: 24px; height: 44px; border-radius: 3px; }
  .member-strip__badge--round { width: 26px; height: 26px; border-radius: 50%; background: #777; }
  .member-strip__badge--flat { width: 58px; height: 18px; background: #c9d98a; }
  .member-strip__name { font-size: 10px; color: #2f4f9a; letter-spacing: 1.5px; }
  .member-strip__group { display: flex; align-items: center; gap: 5px; }
  .member-strip__small { font-size: 8px; color: var(--ink); }

  .contact-footer {
    position: absolute; left: 0; bottom: 0; width: 100%; height: 72px;
    background: var(--footer-grey); color: #fff;
    font-size: 8px; line-height: 1.4; text-align: center;
    padding: 16px 0 0 64px;
  }

  /* ---------- sale flyer ---------- */
  .sale-flyer {
    position: absolute; left: 630px; top: 72px;
    width: 325px; height: 646px;
    background: var(--sale-red);
    overflow: hidden; color: #fff;
  }
  .sale-flyer__brand {
    position: absolute; left: 70px; top: 40px;
    font-size: 20px; font-weight: 400; letter-spacing: 2.4px;
  }
  .sale-flyer__mark {
    position: absolute; left: 24px; top: 38px; width: 26px; height: 26px;
    background: #fff;
  }
  .sale-flyer__rule {
    position: absolute; left: 0; right: 16px; top: 78px;
    border-top: 1px solid rgba(255,255,255,.9);
  }
  .sale-flyer__season {
    position: absolute; left: 20px; top: 92px;
    font-size: 20px; line-height: 1.3; text-transform: uppercase;
  }
  .sale-flyer__season strong { font-weight: 800; display: block; }
  .sale-flyer__headline {
    position: absolute; right: 20px; top: 80px;
    font-size: 62px; font-weight: 800; letter-spacing: 1px; line-height: 1.2;
  }
  .sale-flyer__room {
    position: absolute; left: 0; top: 165px; width: 100%; height: 455px;
    background: linear-gradient(165deg, var(--room-light) 0%, var(--room-wood) 50%, var(--room-light) 100%);
  }
  .sale-flyer__pointer { position: absolute; left: 140px; top: 164px; }
  .sale-flyer__from {
    position: absolute; left: 28px; top: 492px;
    color: var(--sale-red); font-size: 15px; font-weight: 700; line-height: 1.2;
    text-shadow: 0 0 3px #fff, 0 0 3px #fff;
  }
  .sale-flyer__price {
    position: absolute; left: 34px; top: 516px;
    color: var(--sale-red); font-size: 64px; font-weight: 600; line-height: 1;
    text-shadow: 0 0 4px #fff, 0 0 3px #fff, 0 0 2px #fff;
  }
  .sale-flyer__price .cents { display: inline-block; vertical-align: top; font-size: 42px; line-height: .9; }
  .sale-flyer__price .unit { display: block; font-size: 22px; font-weight: 700; }
  .sale-flyer__web {
    position: absolute; left: 0; bottom: 0; width: 100%; height: 26px;
    text-align: center; font-size: 12px; font-weight: 600; line-height: 26px;
  }
</style>
</head>
<body>

<section class="price-flyer" aria-label="Larchvale Surfaces price list">
  <div class="price-flyer__carpet" role="img" aria-label="Close-up photograph of cream shag carpet"></div>
  <div class="price-flyer__wood" role="img" aria-label="Photograph of warm brown hardwood planks"></div>

  <header class="brand-header">
    <span class="brand-header__mark"></span>
    <span class="brand-header__name">larchvalesurfaces</span>
    <span class="brand-header__rule"></span>
  </header>

  <div class="special" style="top:80px;height:62px">
    <p class="special__name">Multicolor Berber Carpet</p>
    <p class="special__detail">2 Styles, 24 colors</p>
    <span class="special__was" style="left:140px;top:44px">$2.39</span>
    <span class="special__now" style="top:-6px;font-size:48px">$1<span class="cents" style="font-size:32px">59<span class="unit" style="font-size:13px">sq ft</span></span></span>
  </div>

  <div class="special" style="top:160px;height:44px">
    <p class="special__name">35oz Plush Velmora Carpet</p>
    <p class="special__detail">2 Styles, 30 Colors</p>
    <span class="special__was" style="left:160px;top:20px">$2.89</span>
    <span class="special__now" style="top:-4px;font-size:34px">$1<span class="cents" style="font-size:22px">99<span class="unit" style="font-size:10px">sq ft</span></span></span>
  </div>

  <div class="special" style="top:210px;height:44px">
    <p class="special__name">Patterned Velmora Carpet</p>
    <p class="special__detail">12 Colors</p>
    <span class="special__was" style="left:160px;top:20px">$2.99</span>
    <span class="special__now" style="top:-4px;font-size:34px">$1<span class="cents" style="font-size:22px">99<span class="unit" style="font-size:10px">sq ft</span></span></span>
  </div>

  <div class="special" style="top:260px;height:44px">
    <p class="special__name">50oz Freize Velmora Carpet</p>
    <p class="special__detail">2 Styles, 28 Colors</p>
    <span class="special__was" style="left:160px;top:20px">$2.99</span>
    <span class="special__now" style="top:-4px;font-size:34px">$2<span class="cents" style="font-size:22px">39<span class="unit" style="font-size:10px">sq ft</span></span></span>
  </div>

  <div class="special" style="top:310px;height:44px;border-bottom:none">
    <p class="special__name">Dustquell Berber Carpet</p>
    <p class="special__detail">12 Colors</p>
    <span class="special__was" style="left:160px;top:26px">$3.59</span>
    <span class="special__now" style="top:-4px;font-size:34px">$2<span class="cents" style="font-size:22px">39<span class="unit" style="font-size:10px">sq ft</span></span></span>
  </div>

  <div class="special special--wood" style="top:385px;height:46px">
    <p class="special__name">5” Designer Engineered Hardwood</p>
    <p class="special__detail">10 different styles</p>
    <span class="special__was" style="left:170px;top:28px">$6.25</span>
    <span class="special__now" style="top:4px;font-size:34px">$4<span class="cents" style="font-size:22px">99<span class="unit" style="font-size:10px">sq ft</span></span></span>
  </div>

  <div class="special special--wood" style="top:440px;height:52px">
    <p class="special__name">12” x 36” Commercial-Grad<br>Vinyl Cork Planking</p>
    <span class="origin-tag" role="img" aria-label="Swiss-made tag"></span>
    <span class="special__was" style="left:170px;top:30px">$6.75</span>
    <span class="special__now" style="top:4px;font-size:34px">$3<span class="cents" style="font-size:22px">99<span class="unit" style="font-size:10px">sq ft</span></span></span>
  </div>

  <div class="member-strip" aria-label="Memberships">
    <span class="member-strip__group"><span class="member-strip__badge member-strip__badge--tall" role="img" aria-label="OZJ accreditation badge"></span></span>
    <span class="member-strip__name">QUILLMARK</span>
    <span class="member-strip__group"><span class="member-strip__badge member-strip__badge--round" role="img" aria-label="PQHU membership badge"></span><span class="member-strip__small">PQHU</span></span>
    <span class="member-strip__badge member-strip__badge--flat" role="img" aria-label="Rimhold Surface covering guild badge"></span>
  </div>

  <footer class="contact-footer">
    <p>48 Tamsin Row, Eastbrook, QX, R2K 7L4</p>
    <p>Phone: 555 014 0011 &nbsp; Fax: 555 014 0556</p>
    <p>contact@larchvalesurfaces.example</p>
    <p>www.larchvalesurfaces.example</p>
  </footer>
</section>

<section class="sale-flyer" aria-label="Winter flooring sale">
  <span class="sale-flyer__mark"></span>
  <span class="sale-flyer__brand">larchvalesurfaces</span>
  <span class="sale-flyer__rule"></span>
  <p class="sale-flyer__season"><strong>Winter</strong>Flooring</p>
  <p class="sale-flyer__headline">SALE</p>

  <div class="sale-flyer__room" role="img" aria-label="Photograph of a bright living room with white sofas, glass coffee table, shag rug and dark hardwood floor"></div>
  <svg class="sale-flyer__pointer" width="44" height="24" viewBox="0 0 44 24" aria-hidden="true">
    <polygon points="0,0 44,0 22,24" fill="#e31e26"/>
  </svg>

  <p class="sale-flyer__from">prices from</p>
  <p class="sale-flyer__price">$1<span class="cents">59<span class="unit">sq ft</span></span></p>

  <footer class="sale-flyer__web">www.larchvalesurfaces.example</footer>
</section>

</body>
</html>
```